TREVAL BUILDWORKS, LLC Webpage portfolio

I want to create a Website that allows my potential clients to browse my Skilled work via before and after photos. I want the website to enhance the work that I provide and potentially drive new business, or at least solidify my work.
I also do 3D CAD and Modeling of New Spaces and it would be nice to show some of that work from pencil design to 3D modeling, which I feel may help give me more clients.

The website needs to show a solid carpenter/company with the skills to get any project completed.

Types of Jobs - Custom Carpentry & Finishes, Kitchens, Baths, Basements, Decks, Porches, Whole House Renovation - Skilled Craftsmanship (Hardwood Flooring, Floor and Wall Tile) and much more...

Target Market(s)

Residential Home Renovation, Kitchen and Bath Renovation, Home Improvement

Industry/Entity Type

Residential Construction

Number of Pages Required

5+ page

Font styles to use
Sans Serif
Script

Requirements
Must have
• Similar to Plinvo.com, except for Treval Buildworks.
• Must be inviting.
• My Services Offered
• A way to reach me or contact me for estimates with some sort of Screening Questionare.
Nice to have
• Inviting Colors
Should not have
• Not sure at this time

```html
<!DOCTYPE html>
<html lang="en">
<head>
<meta charset="utf-8">
<title>Treval Buildworks — Home Renovation &amp; Craftsmanship</title>
<link href="https://fonts.googleapis.com/css2?family=Raleway:wght@500;600;700;800&family=Open+Sans:wght@400;600;700&display=swap" rel="stylesheet">
<style>
:root{
  --navy:#0f2740;
  --navy-deep:#0b1b2e;
  --blue:#2f80d1;
  --blue-bar:#2b7fcf;
  --green:#4dab3c;
  --page:#f1f1f1;
  --panel:#e8e8e8;
  --card:#ffffff;
  --ink:#2b2b2b;
  --muted:#7a7a7a;
  --line:#dddddd;
}
*{box-sizing:border-box;margin:0;padding:0}
html,body{width:1200px;height:4478px;overflow:hidden}
body{background:var(--page);font-family:"Open Sans",Arial,sans-serif;color:var(--ink);position:relative}
.wrap{position:absolute;left:164px;width:872px}
h2.section-title{position:absolute;left:0;width:1200px;text-align:center;font-family:"Raleway",Arial,sans-serif;font-weight:600;font-size:22px;color:#333}

/* header */
.site-header{position:absolute;top:0;left:0;width:1200px;height:113px;background:#fff}
.brand{position:absolute;left:164px;top:26px;display:flex;align-items:center;gap:10px}
.brand-mark{width:34px;height:34px;background:var(--navy)}
.brand-name{font-family:"Raleway",sans-serif;font-weight:800;font-size:22px;color:var(--navy);line-height:1}
.brand-tag{position:absolute;left:164px;top:66px;font-size:8px;letter-spacing:1.2px;color:var(--muted);font-family:"Raleway",sans-serif;font-weight:600}
.top-contact{position:absolute;top:26px;left:700px;font-family:"Raleway",sans-serif;font-size:13px;font-weight:600;color:#333}
.top-actions{position:absolute;top:22px;right:164px;display:flex;gap:8px}
.btn-small{font-size:10px;font-weight:700;color:#fff;padding:6px 12px;text-transform:uppercase;letter-spacing:.5px}
.btn-login{background:var(--blue)}
.btn-join{background:var(--navy)}
.main-nav{position:absolute;top:76px;left:452px;display:flex;gap:40px;font-family:"Raleway",sans-serif;font-size:11px;font-weight:700;color:#444;letter-spacing:.5px}
.main-nav .active{color:var(--blue);border-bottom:2px solid var(--blue);padding-bottom:6px}

/* hero */
.hero{position:absolute;top:113px;left:0;width:1200px;height:499px;background:linear-gradient(160deg,#3b2414 0%,#6a3f22 35%,#4a2c18 60%,#241409 100%)}
.hero-title{position:absolute;top:364px;width:1200px;text-align:center;font-family:"Raleway",sans-serif;font-weight:800;font-size:34px;color:#fff;letter-spacing:1px}
.hero-actions{position:absolute;top:440px;left:343px;display:flex;gap:21px}
.hero-btn{width:224px;height:36px;display:flex;align-items:center;justify-content:center;gap:8px;color:#fff;font-size:12px;font-weight:600;border-radius:3px}
.hero-btn.email{background:var(--green)}
.hero-btn.social{background:var(--blue)}
.hero-arrow{position:absolute;top:336px}

/* features */
.features-title{top:656px}
.feature{position:absolute;top:720px;width:300px;text-align:center}
.feature h3{font-family:"Raleway",sans-serif;font-weight:600;font-size:17px;margin-top:18px;color:#333}
.feature p{font-size:10.5px;line-height:1.7;color:#666;margin-top:12px}

/* cards */
.card{position:absolute;background:var(--card);width:278px}
.card-photo{height:170px}
.card-body{padding:18px 14px 0}
.card-title{font-family:"Raleway",sans-serif;font-weight:700;font-size:13px;color:#222}
.card-text{font-size:10px;line-height:1.7;color:#777;margin-top:12px;height:36px}
.card-meta{display:flex;justify-content:space-between;font-size:8.5px;color:#999;margin-top:14px;border-top:1px solid #eee;padding-top:10px}
.card.short{height:289px}

.browse-box{position:absolute;background:#fff;width:576px;height:300px;padding:18px 16px}
.browse-box h4{font-family:"Raleway",sans-serif;font-size:13px;font-weight:700;color:#222}
.browse-box p{font-size:9.5px;line-height:1.9;color:#555;margin:10px 0 20px}
.help-card{position:absolute;width:278px;height:300px;background:linear-gradient(150deg,#3a2618,#6b4630 55%,#2b1b10)}
.help-card h4{position:absolute;left:66px;top:100px;font-family:"Raleway",sans-serif;font-weight:600;font-size:21px;line-height:1.3;color:#fff}
.help-card .btn-advice{position:absolute;left:96px;top:172px;background:var(--blue);color:#fff;font-size:11px;font-weight:600;padding:8px 14px;border-radius:3px}

.wide-card{position:absolute;background:#fff;width:872px;height:254px}
.wide-card h3{position:absolute;left:16px;top:40px;width:330px;font-family:"Raleway",sans-serif;font-weight:700;font-size:14px;line-height:1.5;color:#222}
.wide-card p{position:absolute;left:16px;top:120px;width:330px;font-size:10px;line-height:1.8;color:#777}
.view-more{position:absolute;top:2284px;left:552px;width:96px;height:30px;background:var(--blue);color:#fff;font-size:11px;font-weight:600;border-radius:15px;display:flex;align-items:center;justify-content:center}

/* before/after */
.ba-title{top:2372px}
.ba-intro{position:absolute;top:2414px;left:230px;width:740px;text-align:center;font-size:10px;line-height:1.8;color:#666}
.ba-panel{position:absolute;top:2501px;width:428px;height:314px;display:flex}
.ba-panel div.half{flex:1}
.ba-badge{position:absolute;bottom:22px;width:66px;height:66px;border-radius:50%;display:flex;align-items:center;justify-content:center;color:#fff;font-size:12px;font-weight:600}
.ba-badge.before{left:14px;background:var(--navy)}
.ba-badge.after{right:14px;background:var(--blue)}
.slide-arrow{position:absolute;top:2648px}

/* types of jobs */
.jobs-title{top:2894px}
.much-more{position:absolute;background:#fff;width:278px;height:215px;padding:16px}
.much-more h4{font-family:"Raleway",sans-serif;font-size:13px;font-weight:700}
.much-more ul{list-style:none;display:grid;grid-template-columns:1fr 1fr;gap:9px 6px;margin-top:16px;font-size:9.5px;color:#555}

/* footer browse */
.footer-browse{position:absolute;top:3866px;left:0;width:1200px;height:380px;background:var(--panel)}
.fb-heading{position:absolute;top:46px;font-family:"Raleway",sans-serif;font-size:15px;font-weight:700;color:#222}
.fb-col{position:absolute;top:84px;list-style:none;font-size:9.5px;line-height:2;color:#444}
.fb-category{position:absolute;top:284px;left:164px;width:872px}
.fb-category h5{font-family:"Raleway",sans-serif;font-size:13px;font-weight:700}
.fb-category p{font-size:9px;line-height:1.9;color:#555;margin-top:6px}

/* dark footer */
.footer-main{position:absolute;top:4246px;left:0;width:1200px;height:196px;background:var(--navy-deep)}
.partners{position:absolute;top:48px;left:320px;display:flex;gap:36px;align-items:center}
.partner{background:#5b6b7e;opacity:.75}
.footer-links{position:absolute;top:116px;width:1200px;text-align:center;font-size:9.5px;color:#cfd8e2}
.footer-links span{margin:0 10px}
.copyright{position:absolute;top:146px;width:1200px;text-align:center;font-size:9px;color:#9fb0c2}
.bottom-bar{position:absolute;top:4442px;left:0;width:1200px;height:36px;background:var(--blue-bar);color:#fff;font-size:9.5px}
.network{position:absolute;left:164px;top:11px;display:flex;align-items:center;gap:8px}
.network i{width:12px;height:12px;border-radius:50%;background:#fff;opacity:.85;display:inline-block}
.bar-links{position:absolute;right:164px;top:11px;display:flex;gap:30px}
</style>
</head>
<body>

<header class="site-header">
  <div class="brand"><span class="brand-mark"></span><span class="brand-name">Treval Buildworks</span></div>
  <div class="brand-tag">GENERAL BUILD &amp; REMODELING CONTRACTOR</div>
  <div class="top-contact">CALL US: 555-013-2746</div>
  <div class="top-actions"><span class="btn-small btn-login">Login</span><span class="btn-small btn-join">Join Now</span></div>
  <nav class="main-nav">
    <span class="active">HOME</span><span>PHOTOS</span><span>3D MODELLING</span><span>PROFESSIONALS</span><span>STORIES &amp; ADVICE</span><span>JOBS</span>
  </nav>
</header>

<section class="hero" role="img" aria-label="Warm wooden kitchen interior with pendant lights and cabinetry">
</section>
<svg class="hero-arrow" style="left:40px" width="24" height="44" viewBox="0 0 24 44"><path d="M20 2 L4 22 L20 42" fill="none" stroke="#fff" stroke-width="3"/></svg>
<svg class="hero-arrow" style="left:1136px" width="24" height="44" viewBox="0 0 24 44"><path d="M4 2 L20 22 L4 42" fill="none" stroke="#fff" stroke-width="3"/></svg>
<h1 class="hero-title">THE NEW WAY TO DESIGN YOUR HOME</h1>
<div class="hero-actions">
  <span class="hero-btn email"><svg width="14" height="10" viewBox="0 0 14 10"><rect x="0.5" y="0.5" width="13" height="9" fill="none" stroke="#fff"/><path d="M1 1 L7 6 L13 1" fill="none" stroke="#fff"/></svg>Sign Up with Email</span>
  <span class="hero-btn social">Continue with Linkory</span>
</div>

<h2 class="section-title features-title">Create the Home you've Always Wanted</h2>
<div class="feature" style="left:134px">
  <svg width="44" height="40" viewBox="0 0 44 40"><path d="M4 20 L22 4 L40 20 M9 16 V36 H35 V16 M18 36 V24 H26 V36" fill="none" stroke="#333" stroke-width="2"/></svg>
  <h3>Finibusnorum</h3>
  <p>Plan every room with trusted builders and clear ideas for a home designed around the way you live.</p>
</div>
<div class="feature" style="left:450px">
  <svg width="44" height="40" viewBox="0 0 44 40"><path d="M12 36 L12 8 L18 2 L24 8 V36 Z M30 36 V4 H38 V36 Z M30 12 H34 M30 20 H34 M30 28 H34" fill="none" stroke="#333" stroke-width="2"/></svg>
  <h3>Finibusnorum</h3>
  <p>From pencil sketch to full 3D model, see your new space before a single board is cut.</p>
</div>
<div class="feature" style="left:766px">
  <svg width="44" height="40" viewBox="0 0 44 40"><path d="M6 30 A16 16 0 0 1 38 30 Z M4 30 H40 V34 H4 Z M20 14 V8 H24 V14" fill="none" stroke="#333" stroke-width="2"/></svg>
  <h3>Finibusnorum</h3>
  <p>Skilled crews finish each project on schedule with careful work that stands the test of time.</p>
</div>

<h2 class="section-title" style="top:988px">Treval Buildworks</h2>

<!-- portfolio row 1 -->
<div class="card short" style="left:164px;top:1039px">
  <div class="card-photo" role="img" aria-label="Custom wooden doorway and trim work" style="background:linear-gradient(135deg,#8a6a4a,#d8c6ac 60%,#6c4f35)"></div>
  <div class="card-body"><div class="card-title">Custom Carpentry &amp; Finishes</div><p class="card-text">Skilled trim, built-ins and finish work crafted for homes that last.</p><div class="card-meta"><span>10 hours ago</span><span>18 Bookmarks | 3 Comments</span></div></div>
</div>
<div class="card short" style="left:461px;top:1039px">
  <div class="card-photo" role="img" aria-label="Renovated kitchen with dark wood cabinets" style="background:linear-gradient(135deg,#2e1a10,#6b3d22 55%,#3a2416)"></div>
  <div class="card-body"><div class="card-title">Kitchens</div><p class="card-text">Skilled trim, built-ins and finish work crafted for homes that last.</p><div class="card-meta"><span>10 hours ago</span><span>18 Bookmarks | 3 Comments</span></div></div>
</div>
<div class="card short" style="left:758px;top:1039px">
  <div class="card-photo" role="img" aria-label="House exterior with grey siding" style="background:linear-gradient(135deg,#6a6f7a,#a7acb5 55%,#4f5560)"></div>
  <div class="card-body"><div class="card-title">Rustic Products</div><p class="card-text">Skilled trim, built-ins and finish work crafted for homes that last.</p><div class="card-meta"><span>10 hours ago</span><span>18 Bookmarks | 3 Comments</span></div></div>
</div>

<!-- row 2 -->
<div class="browse-box" style="left:164px;top:1358px">
  <h4>Browse Photos</h4>
  <p>Kitchen · Bathroom · Powder Room · Bedroom · Living Room · Home Theater · Family Room · Dining · Deck · Patio · Pool · Sunroom · Landscape · Porch · Baby &amp; Kids · Nursery · Home Office · Storage &amp; Closet · Exterior · Basement · Entry · Garage &amp; Shed · Gym · Hall · Home Bar · Laundry · Staircase · Wine Cellar · Topics</p>
  <h4>Browse Products</h4>
  <p>Sofas · Chairs · Coffee &amp; Accent Tables · Dining Tables · Dining Chairs · Beds &amp; Headboards · Nightstands &amp; Bedside Tables · Dressers · Bedding · Desks · Office Chairs · Lighting · Kitchen Appliances · Cookware · Bakeware · Kitchen Knives &amp; Accessories · Dinnerware · Serveware · Cups &amp; Glassware · Wine &amp; Bar Tools · Pillows &amp; Throws · Wallpaper · More</p>
</div>
<div class="help-card" role="img" aria-label="Warm-lit renovated living space" style="left:758px;top:1358px">
  <h4>Need help with<br>your project?</h4>
  <span class="btn-advice">Get Advice</span>
</div>

<!-- row 3 -->
<div class="card short" style="left:164px;top:1672px">
  <div class="card-photo" role="img" aria-label="Basement staircase with white railings" style="background:linear-gradient(135deg,#8c7a62,#e2d8c8 55%,#9b8668)"></div>
  <div class="card-body"><div class="card-title">Basements</div><p class="card-text">Skilled trim, built-ins and finish work crafted for homes that last.</p><div class="card-meta"><span>10 hours ago</span><span>18 Bookmarks | 3 Comments</span></div></div>
</div>
<div class="card short" style="left:461px;top:1672px">
  <div class="card-photo" role="img" aria-label="Pencil 3D model drawing of a house" style="background:linear-gradient(135deg,#f4f4f4,#d2d2d2 55%,#ececec)"></div>
  <div class="card-body"><div class="card-title">3D Modeling</div><p class="card-text">Skilled trim, built-ins and finish work crafted for homes that last.</p><div class="card-meta"><span>10 hours ago</span><span>18 Bookmarks | 3 Comments</span></div></div>
</div>
<div class="card short" style="left:758px;top:1672px">
  <div class="card-photo" role="img" aria-label="Porch ceiling with hanging glass lights" style="background:linear-gradient(135deg,#3a2a1e,#8a6a4c 55%,#2d1f16)"></div>
  <div class="card-body"><div class="card-title">Porches</div><p class="card-text">Skilled trim, built-ins and finish work crafted for homes that last.</p><div class="card-meta"><span>10 hours ago</span><span>18 Bookmarks | 3 Comments</span></div></div>
</div>

<!-- row 4 -->
<div class="wide-card" style="left:164px;top:2000px">
  <h3>Sed ut perspiciatis unde omnis iste natus volup tatem accusantium doloremque</h3>
  <p>See how a plan grows from rough pencil lines into a detailed 3D model, giving you a clear view of your new space before construction begins.</p>
  <div role="img" aria-label="Pencil wireframe drawing of a house" style="position:absolute;left:420px;top:40px;width:200px;height:174px;background:linear-gradient(135deg,#fafafa,#dcdcdc)"></div>
  <div role="img" aria-label="Rendered 3D model of a finished house" style="position:absolute;left:640px;top:40px;width:216px;height:174px;background:linear-gradient(135deg,#d9d2c2,#a07a50 55%,#6e8a5a)"></div>
</div>
<div class="view-more">View More</div>

<!-- before & after -->
<h2 class="section-title ba-title">Before and After Photos</h2>
<p class="ba-intro">Browse finished projects side by side. Every space shows where the work began and how careful planning, quality materials and skilled hands turned an old room into one built to enjoy for years to come.</p>
<svg class="slide-arrow" style="left:98px" width="14" height="24" viewBox="0 0 14 24"><path d="M12 2 L2 12 L12 22" fill="none" stroke="#666" stroke-width="2.5"/></svg>
<svg class="slide-arrow" style="left:1088px" width="14" height="24" viewBox="0 0 14 24"><path d="M2 2 L12 12 L2 22" fill="none" stroke="#666" stroke-width="2.5"/></svg>
<div class="ba-panel" style="left:164px">
  <div class="half" role="img" aria-label="Room before renovation" style="background:linear-gradient(135deg,#3b2a1c,#7a5a3c 60%,#2e2015)"></div>
  <div class="half" role="img" aria-label="Room after renovation" style="background:linear-gradient(135deg,#5a3018,#b0683a 55%,#3a2010)"></div>
  <span class="ba-badge before">Before</span><span class="ba-badge after">After</span>
</div>
<div class="ba-panel" style="left:608px">
  <div class="half" role="img" aria-label="Kitchen before renovation" style="background:linear-gradient(135deg,#2c1e14,#5e4430 60%,#22170f)"></div>
  <div class="half" role="img" aria-label="Kitchen after renovation" style="background:linear-gradient(135deg,#4a3020,#8a6446 55%,#2c1c12)"></div>
  <span class="ba-badge before">Before</span><span class="ba-badge after">After</span>
</div>

<!-- types of jobs -->
<h2 class="section-title jobs-title">Types of Jobs</h2>
<div class="card" style="left:164px;top:2955px;height:293px">
  <div class="card-photo" role="img" aria-label="Custom wood cabinetry with warm lighting" style="background:linear-gradient(135deg,#3a1e0e,#a0602e 55%,#4a2812)"></div>
  <div class="card-body"><div class="card-title">Custom Carpentry &amp; Finishes</div><p class="card-text">Skilled trim, built-ins and finish work crafted for homes that last.</p><div class="card-meta"><span>10 hours ago</span><span>18 Bookmarks | 3 Comments</span></div></div>
</div>
<div class="card" style="left:461px;top:2955px;height:293px">
  <div class="card-photo" role="img" aria-label="Kitchen with dark cabinets and island" style="background:linear-gradient(135deg,#24150c,#5c3820 55%,#2a190e)"></div>
  <div class="card-body"><div class="card-title">Kitchens</div><p class="card-text">Skilled trim, built-ins and finish work crafted for homes that last.</p><div class="card-meta"><span>10 hours ago</span><span>18 Bookmarks | 3 Comments</span></div></div>
</div>
<div class="card" style="left:758px;top:2955px;height:293px">
  <div class="card-photo" role="img" aria-label="Bathroom with wood vanity and mirror" style="background:linear-gradient(135deg,#4a2a18,#9a6a44 55%,#3a2214)"></div>
  <div class="card-body"><div class="card-title">Baths</div><p class="card-text">Skilled trim, built-ins and finish work crafted for homes that last.</p><div class="card-meta"><span>10 hours ago</span><span>18 Bookmarks | 3 Comments</span></div></div>
</div>
<div class="card" style="left:164px;top:3269px;height:283px">
  <div class="card-photo" role="img" aria-label="Basement finished with stairs and railings" style="background:linear-gradient(135deg,#7a6450,#c9b59a 55%,#6a5440)"></div>
  <div class="card-body"><div class="card-title">Basements</div><p class="card-text">Skilled trim, built-ins and finish work crafted for homes that last.</p><div class="card-meta"><span>10 hours ago</span><span>18 Bookmarks | 3 Comments</span></div></div>
</div>
<div class="card" style="left:461px;top:3269px;height:283px">
  <div class="card-photo" role="img" aria-label="Wooden backyard deck" style="background:linear-gradient(135deg,#5a4030,#9a7a5a 55%,#6a8a5a)"></div>
  <div class="card-body"><div class="card-title">Decks</div><p class="card-text">Skilled trim, built-ins and finish work crafted for homes that last.</p><div class="card-meta"><span>10 hours ago</span><span>18 Bookmarks | 3 Comments</span></div></div>
</div>
<div class="card" style="left:758px;top:3269px;height:283px">
  <div class="card-photo" role="img" aria-label="Covered porch with posts and railings" style="background:linear-gradient(135deg,#6a6a6a,#b8b4aa 55%,#4a4a4a)"></div>
  <div class="card-body"><div class="card-title">Porches</div><p class="card-text">Skilled trim, built-ins and finish work crafted for homes that last.</p><div class="card-meta"><span>10 hours ago</span><span>18 Bookmarks | 3 Comments</span></div></div>
</div>
<div class="wide-card" style="left:164px;top:3582px;width:576px;height:215px">
  <h3 style="top:36px;width:260px">Whole House Renovation - Skilled Craftsmanship</h3>
  <p style="top:100px;width:270px">Hardwood flooring, floor and wall tile and complete remodels handled by one crew from start to finish.</p>
  <div role="img" aria-label="Renovated interior with hardwood floors" style="position:absolute;left:300px;top:0;width:276px;height:215px;background:linear-gradient(135deg,#1e120a,#6a4228 55%,#2a1a0e)"></div>
</div>
<div class="much-more" style="left:758px;top:3582px">
  <h4>Much More...</h4>
  <ul>
    <li>Nam fringilla ante</li><li>Nam fringilla ante</li>
    <li>Maximus feugiat</li><li>Maximus feugiat</li>
    <li>Vestibulum vitae</li><li>Vestibulum vitae</li>
    <li>Wal blandit rhoncus</li><li>Wal blandit rhoncus</li>
    <li>Quis sit amet libero</li><li>Quis sit amet libero</li>
  </ul>
</div>

<!-- footer browse -->
<section class="footer-browse">
  <div class="fb-heading" style="left:164px">Browse Professionals</div>
  <ul class="fb-col" style="left:164px"><li>Albuquerque</li><li>Atlanta - Austin</li><li>Baltimore - Birmingham</li><li>Boise - Boston</li><li>Bridgeport - Burlington</li><li>Cedar Rapid</li></ul>
  <ul class="fb-col" style="left:316px"><li>San Luis Obispo</li><li>Santa Barbara - Seattle</li><li>St Louis - Tampa - Wichita</li><li>Wilmington - Calgary</li><li>Edmonton - Montreal</li><li>Ottawa - Toronto</li></ul>
  <ul class="fb-col" style="left:478px"><li>Vancouver - Prov By City</li><li>San Luis Obispo</li><li>Santa Barbara - Seattle</li><li>St Louis - Tampa - Wichita</li><li>Wilmington - Calgary</li><li>Edmonton - Montreal</li></ul>
  <div class="fb-heading" style="left:672px">Browse Products</div>
  <ul class="fb-col" style="left:672px"><li>Sofas - Chairs</li><li>Coffee &amp; Accent Tables</li><li>Dining Tables - Dining Chairs</li><li>Beds &amp; Headboards</li><li>Nightstands &amp; Bedside Tables</li><li>Dressers - Bedding</li></ul>
  <ul class="fb-col" style="left:875px"><li>Kitchen Appliances - Cookware</li><li>Bakeware - Kitchen Knives</li><li>Accessories - Dinnerware</li><li>Serveware - Cups &amp; Glassware</li><li>Wine &amp; Bar Tools</li><li>Pillows &amp; Throws - More</li></ul>
  <div class="fb-category">
    <h5>By Category:</h5>
    <p>Kitchen &amp; Bath Designers - Kitchen &amp; Bath Remodelers - Landscape Architects &amp; Landscape Designers - Landscape Contractors - Swimming Pool Builders Kitchen &amp; Bath Designers - Kitchen &amp; Bath Remodelers - Landscape Architects &amp; Landscape Designers - Landscape Contractors - Swimming Pool Builders. Find a trusted local pro for every room and every renovation project you plan.</p>
  </div>
</section>

<!-- main footer -->
<footer class="footer-main">
  <div class="partners">
    <span class="partner" style="width:34px;height:34px;border-radius:4px"></span>
    <span class="partner" style="width:130px;height:14px"></span>
    <span class="partner" style="width:30px;height:30px;border-radius:50%"></span>
    <span class="partner" style="width:110px;height:14px"></span>
    <span class="partner" style="width:30px;height:30px;border-radius:50%"></span>
  </div>
  <div class="footer-links"><span>Custom Carpentry &amp; Finishes</span>|<span>Kitchens</span>|<span>Baths</span>|<span>Basements</span>|<span>Decks</span>|<span>Porches</span>|<span>Whole House Renovation - Skilled Craftsmanship</span></div>
  <div class="copyright">© 2017 Treval Buildworks. All Copyrights are Reserved. Privacy Policy | Terms &amp; Conditions Email: info@trevalbuildworks.com, Phone:555-013-8842</div>
</footer>
<div class="bottom-bar">
  <div class="network">Network with us <i></i><i></i><i></i><i></i></div>
  <div class="bar-links"><span>Get Help</span><span>Site Feedback</span><span>Newsletter Signup</span><span>Free App Download</span><span>Quick Links</span><span>US</span></div>
</div>

</body>
</html>
```